Wholesale in Gold Jewellery & Gold Bullion

We are an established gold jewellery and gold bullion wholesaler selling these products to international clients. We already have a name and logo of our company, hence please view attached current card design. We need a completely new design to compliment our business and industry and the final design should be new and elegant.

Contact Information for Business Card

New card details must be same as per current card. Like logo, name, tel no. & etc.

Colors

Designer to choose colors to be used in the design.

```html
<!DOCTYPE html>
<html lang="en">
<head>
<meta charset="utf-8">
<title>Halvern &amp; Co — Business Card</title>
<link rel="stylesheet" href="https://fonts.googleapis.com/css2?family=Montserrat:wght@400;500;600&family=Tinos:wght@700&display=swap">
<style>
  :root {
    --backdrop: #ece8e1;
    --card-white: #f4f4f2;
    --gold-light: #e8bb45;
    --gold-deep: #dc9f22;
    --brown: #2e1c17;
    --ink-white: #fffaf0;
  }
  * { margin: 0; padding: 0; box-sizing: border-box; }
  html, body {
    width: 1200px; height: 900px; overflow: hidden;
    background: var(--backdrop);
  }
  .card {
    position: absolute; left: 100px; top: 164px;
    width: 1000px; height: 572px;
    background: var(--card-white);
    box-shadow: 0 14px 40px rgba(60, 40, 20, 0.18);
    overflow: hidden;
  }
  .card__top {
    position: absolute; left: 0; top: 0; width: 100%; height: 250px;
    display: flex; align-items: center; justify-content: center; gap: 30px;
  }
  .brand__dot {
    width: 92px; height: 92px; border-radius: 50%;
    background: var(--gold-light);
  }
  .brand__name {
    font-family: "Tinos", "Times New Roman", serif;
    font-weight: 700; font-size: 40px; letter-spacing: 0.5px;
    color: var(--brown);
  }
  .card__rule {
    position: absolute; left: 0; top: 250px; width: 100%; height: 8px;
    background: var(--brown);
  }
  .card__band {
    position: absolute; left: 0; top: 264px; width: 100%; bottom: 0;
    background: linear-gradient(100deg, var(--gold-deep) 0%, var(--gold-light) 45%, var(--gold-deep) 100%);
    font-family: "Montserrat", Arial, sans-serif;
  }
  .holder {
    position: absolute; left: 70px; top: 40px;
  }
  .holder__name {
    font-size: 42px; font-weight: 500; color: var(--brown); letter-spacing: 0.5px;
  }
  .holder__title {
    font-size: 34px; font-weight: 400; color: var(--ink-white); margin-top: 2px;
  }
  .holder__address {
    font-size: 24px; font-weight: 400; color: var(--ink-white); line-height: 1.35; margin-top: 8px;
  }
  .contacts {
    position: absolute; right: 60px; bottom: 34px;
    list-style: none;
  }
  .contacts__item {
    display: flex; align-items: center; justify-content: flex-end; gap: 22px;
    font-size: 25px; color: var(--ink-white); line-height: 1.5; letter-spacing: 0.5px;
  }
  .contacts__icon { width: 26px; height: 26px; flex: none; }
</style>
</head>
<body>
  <article class="card">
    <header class="card__top">
      <span class="brand__dot"></span>
      <span class="brand__name">HALVERN &amp; CO PTE LTD</span>
    </header>
    <div class="card__rule"></div>
    <section class="card__band">
      <div class="holder">
        <p class="holder__name">Arjun Velamkar</p>
        <p class="holder__title">Director</p>
        <p class="holder__address">12 Linden Quay Rd,<br>Singapore 208150</p>
      </div>
      <ul class="contacts">
        <li class="contacts__item">+65 9100 2345
          <svg class="contacts__icon" viewBox="0 0 24 24" aria-label="Mobile"><rect x="6" y="1.5" width="12" height="21" rx="2" fill="none" stroke="#2e1c17" stroke-width="2"/><circle cx="12" cy="19" r="1.2" fill="#2e1c17"/></svg>
        </li>
        <li class="contacts__item">+65 6100 4000
          <svg class="contacts__icon" viewBox="0 0 24 24" aria-label="Telephone"><path d="M6.5 2.5l3 4-2 2.5c1.2 2.8 3.5 5.1 6.5 6.5l2.5-2 4 3-1.5 4c-8 0-16-8-16-16z" fill="#2e1c17"/></svg>
        </li>
        <li class="contacts__item">+65 6100 4011
          <svg class="contacts__icon" viewBox="0 0 24 24" aria-label="Fax"><rect x="6" y="2" width="12" height="8" fill="none" stroke="#2e1c17" stroke-width="2"/><rect x="2" y="10" width="20" height="11" rx="1.5" fill="#2e1c17"/><rect x="6" y="13" width="12" height="2" fill="#e8bb45"/></svg>
        </li>
        <li class="contacts__item">arjun@halvernco.com
          <svg class="contacts__icon" viewBox="0 0 24 24" aria-label="Email"><rect x="2" y="5" width="20" height="14" fill="#2e1c17"/><path d="M2 5l10 8 10-8" fill="none" stroke="#e8bb45" stroke-width="1.6"/></svg>
        </li>
      </ul>
    </section>
  </article>
</body>
</html>
```